Business card design Needed for new logo / Construction business, home extensions and new builds

We need a business card design using our new logo files which i will attach to this project :)

We are a small construction business specialising in home extensions, new builds and property development. We are very ambitious and would appreciate professional and elegant designs for our new business card.

Very serious about using the services on MakerQuarry and recently acquired our new logo from here :)

Please get involved, i will feedback when i can as i am very busy but can respond daily, thanks

Target Market(s)

People that want to build onto their houses, new building developments or adding too their existing property

Industry/Entity Type

Construction

Contact Information for Business Card

Renwick Tolliver Construction, Lionel Ashby (Managing Director), Tel 07822254961, email - info@renwick-tolliver, www.renwick-tolliver.co.uk

Colors

Designer to choose colors to be used in the design.

Requirements
Must have
• I like a deep grey on the back please. A lot of you have provided black from and back, try mixing things up a little. The black looks cool 😎 Thanks

```html
<!DOCTYPE html>
<html lang="en">
<head>
<meta charset="utf-8">
<title>Renwick Tolliver Construction – Business Card</title>
<link rel="stylesheet" href="https://fonts.googleapis.com/css2?family=Open+Sans:wght@400;600;700&display=swap">
<style>
  :root {
    --page-bg: #141417;
    --card-front: #1d1c21;
    --card-back: #26252a;
    --pattern-dark: #1f1e23;
    --pattern-light: #3a393f;
    --gold: #e8a823;
    --gold-light: #f2c14e;
    --silver: #c9c9cc;
    --white: #f4f4f4;
    --divider: #9a9aa0;
  }
  * { margin: 0; padding: 0; box-sizing: border-box; }
  html, body {
    width: 1200px; height: 780px; overflow: hidden;
    background: var(--page-bg);
    font-family: "Open Sans", Arial, sans-serif;
  }
  .canvas {
    position: relative; width: 1200px; height: 780px;
    display: flex; align-items: center; justify-content: center; gap: 40px;
  }
  .card {
    position: relative; width: 530px; height: 310px;
    border-radius: 22px; overflow: hidden;
    border-bottom: 3px solid var(--gold);
    border-left: 2px solid var(--gold);
    box-shadow: 0 14px 30px rgba(0,0,0,.55);
  }
  /* Back */
  .card-back { background: var(--card-back); }
  .back-texture {
    position: absolute; inset: 0;
    background: linear-gradient(160deg, var(--pattern-light) 0%, var(--pattern-dark) 45%, var(--pattern-dark) 100%);
  }
  .back-brand {
    position: absolute; top: 26px; right: 28px;
    display: flex; align-items: center; gap: 8px;
  }
  .brand-square { width: 14px; height: 14px; background: var(--gold); }
  .brand-name {
    font-size: 10px; font-weight: 600; letter-spacing: .08em;
    color: var(--gold); text-transform: uppercase;
  }
  /* Front */
  .card-front { background: var(--card-front); }
  .identity { position: absolute; left: 34px; top: 104px; }
  .person-name { font-size: 34px; font-weight: 700; line-height: 1; letter-spacing: .01em; }
  .person-name .first { color: var(--silver); }
  .person-name .last { color: var(--gold); }
  .person-role { margin-top: 6px; font-size: 16px; font-weight: 400; color: var(--white); }
  .divider {
    position: absolute; left: 292px; top: 70px; width: 1px; height: 120px;
    background: var(--divider);
  }
  .contacts {
    position: absolute; left: 312px; top: 92px; list-style: none;
    display: flex; flex-direction: column; gap: 6px;
  }
  .contacts li {
    display: flex; align-items: center; gap: 9px;
    font-size: 13.5px; color: var(--white);
  }
  .contacts svg { width: 13px; height: 13px; flex: none; }
  .address {
    position: absolute; left: 0; right: 0; bottom: 44px;
    text-align: center; font-size: 15px; color: var(--white);
  }
</style>
</head>
<body>
<main class="canvas">

  <section class="card card-back" aria-label="Card back">
    <div class="back-texture" role="img" aria-label="Repeating tone-on-tone brand monogram pattern across the deep grey back"></div>
    <div class="back-brand">
      <span class="brand-square"></span>
      <span class="brand-name">Renwick Tolliver Construction</span>
    </div>
  </section>

  <section class="card card-front" aria-label="Card front">
    <div class="identity">
      <h1 class="person-name"><span class="first">Lionel</span> <span class="last">Ashby</span></h1>
      <p class="person-role">Managing Director</p>
    </div>

    <div class="divider"></div>

    <ul class="contacts">
      <li>
        <svg viewBox="0 0 16 16" aria-hidden="true"><path fill="#e8a823" d="M3.6 1.5 6 4c.4.4.4 1 0 1.4L4.9 6.5a9 9 0 0 0 4.6 4.6l1.1-1.1c.4-.4 1-.4 1.4 0l2.5 2.4c.4.4.4 1 0 1.4l-1.3 1.3C11 16 0 5 1 2.8L2.2 1.5c.4-.4 1-.4 1.4 0Z"/></svg>
        0782 225 4961
      </li>
      <li>
        <svg viewBox="0 0 16 16" aria-hidden="true"><circle cx="8" cy="8" r="6.5" fill="none" stroke="#e8a823" stroke-width="1.5"/><path d="M1.5 8h13M8 1.5c2.4 2.5 2.4 10.5 0 13M8 1.5c-2.4 2.5-2.4 10.5 0 13" fill="none" stroke="#e8a823" stroke-width="1.2"/></svg>
        info@renwick-tolliver.co.uk
      </li>
      <li>
        <svg viewBox="0 0 16 16" aria-hidden="true"><rect x="1" y="3" width="14" height="10" rx="1" fill="#e8a823"/><path d="M1.5 3.8 8 9l6.5-5.2" fill="none" stroke="#1d1c21" stroke-width="1.3"/></svg>
        www.renwick-tolliver.co.uk
      </li>
    </ul>

    <p class="address">Calder Lane, Westbourne Hallcombe, HC4 7RN</p>
  </section>

</main>
</body>
</html>
```